KRWB new business card design

We need a business card design for our established business which is Australia wide however based in Melbourne. We are a young team of Financial Planners who specialize in Insurance and Basic super advice for people like us.

We are people who help our clients get things done in a timely and cost effective manner whilst having a good time and a laugh along the way.

We would like this to have a consistent feel with our new e-brochure which i have attached from a color and font perspective.

Industry/Entity Type

Business

Requirements
Must have
• We do not need specific address details rather just the states we are in:

VIC/NSW/QLD/TAS
Nice to have
• Curved edge to mate the brochure

```html
<!DOCTYPE html>
<html lang="en">
<head>
<meta charset="utf-8">
<title>KRWB business card</title>
<link href="https://fonts.googleapis.com/css2?family=Arimo:ital,wght@0,400;0,700;1,700&family=PT+Sans&display=swap" rel="stylesheet">
<style>
  :root {
    --stage: #7b5031;
    --label: #1e1e1e;
    --green: #6cbf4a;
    --green-deep: #1f9c4a;
    --green-tag: #7cc242;
    --ink: #333333;
    --ink-soft: #7a7a7a;
    --white: #ffffff;
    --black: #0b0b0b;
  }
  * { margin: 0; padding: 0; box-sizing: border-box; }
  html, body { width: 1200px; height: 788px; overflow: hidden; }
  body { background: var(--stage); font-family: "Arimo", Arial, sans-serif; }
  .stage { position: relative; width: 1200px; height: 788px; }

  .view-label {
    position: absolute; width: 526px; text-align: center;
    font-family: "PT Sans", sans-serif; font-size: 22px; color: var(--label);
  }

  .card {
    position: absolute; width: 526px; height: 301px;
    border-radius: 18px; overflow: hidden;
  }
  .card--front { left: 53px; top: 74px;
    background: radial-gradient(ellipse 60% 70% at 50% 30%, #3c3c3c 0%, #171717 60%, var(--black) 100%); }
  .card--back-one { left: 622px; top: 74px; background: var(--white); }
  .card--back-two { left: 53px; top: 446px; background: var(--white); }
  .card--back-three { left: 622px; top: 446px;
    background: radial-gradient(ellipse 70% 80% at 30% 40%, #2e2e2e 0%, #161616 70%, #0d0d0d 100%); }

  .brand { position: absolute; display: flex; align-items: center; gap: 10px;
    font-weight: 700; color: var(--green); }
  .brand__square { background: var(--green); }

  .card--front .brand { left: 0; width: 526px; top: 60px; justify-content: center; font-size: 46px; }
  .card--front .brand__square { width: 22px; height: 22px; }

  .contact-list { position: absolute; left: 56px; top: 172px; list-style: none;
    color: var(--white); font-size: 13.5px; line-height: 17.5px; }
  .contact-list li { display: flex; align-items: center; gap: 4px; }
  .contact-list svg { width: 10px; height: 10px; fill: var(--white); }

  .reach { position: absolute; left: 372px; top: 203px; color: var(--white);
    font-size: 13px; line-height: 18px; }

  .swoosh { position: absolute; left: 0; top: 0; width: 526px; height: 301px; }
  .adviser { position: absolute; right: 38px; top: 255px; text-align: center; color: var(--white); font-weight: 700; }
  .adviser__name { font-size: 17px; line-height: 20px; }
  .adviser__role { font-size: 13px; line-height: 17px; }

  .card--back-one .brand { left: 40px; width: 220px; top: 118px; justify-content: center; font-size: 48px; }
  .card--back-one .brand__square { width: 24px; height: 24px; }
  .divider { position: absolute; left: 261px; top: 20px; width: 2px; height: 240px;
    background: linear-gradient(to bottom, transparent, #9a9a9a 50%, transparent); }

  .services { position: absolute; list-style: none; font-weight: 700; font-size: 14px; }
  .services__title { font-style: italic; font-size: 18px; margin-bottom: 12px; }
  .services li { height: 34px; }
  .services li::before { content: "\25AA\00a0"; }

  .card--back-one .services { left: 320px; top: 46px; color: var(--ink-soft); }
  .card--back-one .services__title { color: #888; }
  .tag-band { position: absolute; left: 0; bottom: 0; width: 100%; height: 39px;
    background: var(--green); color: var(--white); font-weight: 700; font-size: 14px;
    display: flex; align-items: center; justify-content: center; }

  .ghost-name { position: absolute; left: 0; width: 100%; top: 80px; text-align: center;
    font-weight: 700; font-size: 150px; color: #eef4ea; }
  .card--back-two .services { left: 0; width: 100%; top: 46px; text-align: center; color: var(--ink); }
  .card--back-two .services__title { color: #444; }
  .card--back-two .tagline { position: absolute; left: 0; width: 100%; top: 267px;
    text-align: center; font-weight: 700; font-size: 14px; color: #444; }

  .card--back-three .texture { position: absolute; left: 0; top: 0; width: 526px; height: 301px;
    background: linear-gradient(160deg, rgba(255,255,255,0.04), rgba(0,0,0,0.2)); }
  .card--back-three .brand { left: 40px; width: 250px; top: 110px; justify-content: center; font-size: 56px; }
  .card--back-three .brand__square { width: 26px; height: 26px; }
  .card--back-three .services { left: 314px; top: 24px; color: var(--white); }
  .card--back-three .services__title { font-size: 19px; }
  .card--back-three .tagline { position: absolute; left: 313px; top: 252px;
    font-weight: 700; font-size: 14px; line-height: 18px; color: var(--green-tag); }
</style>
</head>
<body>
<main class="stage">
  <p class="view-label" style="left:53px;top:32px">Front</p>
  <p class="view-label" style="left:622px;top:32px">Back - 1</p>
  <p class="view-label" style="left:53px;top:403px">Back - 2</p>
  <p class="view-label" style="left:622px;top:403px">Back - 3</p>

  <section class="card card--front">
    <div class="brand"><span class="brand__square"></span>KRWB</div>
    <ul class="contact-list">
      <li><svg viewBox="0 0 10 10"><path d="M2 1l2 2-1 1.2a6 6 0 003 3L7.2 6l2 2-1.5 1.5C4.5 9.5.5 5.5.5 2.5z"/></svg>1300 555 014</li>
      <li><svg viewBox="0 0 10 10"><rect x="2" y="0.5" width="6" height="3"/><rect x="0.5" y="3.5" width="9" height="4" rx="1"/><rect x="2.5" y="6.5" width="5" height="3"/></svg>03 9555 0182</li>
      <li><svg viewBox="0 0 10 10"><rect x="3" y="0.5" width="4" height="9" rx="1"/></svg>0400 555 271</li>
      <li><svg viewBox="0 0 10 10"><path d="M0.5 2h9v6h-9z M0.5 2l4.5 3.5L9.5 2" fill="none" stroke="#fff" stroke-width="1"/></svg>dana@krwb.com.au</li>
    </ul>
    <div class="reach">www.krwb.com.au<br>VIC/NSW/QLD/TAS</div>
    <svg class="swoosh" viewBox="0 0 526 301" aria-hidden="true">
      <path d="M0 276 C140 258 310 240 526 262 L526 301 L0 301Z" fill="var(--green)"/>
      <path d="M0 292 C150 276 320 258 526 266 L526 270 C320 264 150 284 0 298Z" fill="#0b0b0b"/>
      <path d="M0 298 C150 284 320 264 526 270 L526 301 L0 301Z" fill="var(--green)"/>
    </svg>
    <div class="adviser">
      <p class="adviser__name">Dana Whitfield</p>
      <p class="adviser__role">ADFS, BBus, LRS© - Financial Adviser</p>
    </div>
  </section>

  <section class="card card--back-one">
    <div class="brand"><span class="brand__square"></span>KRWB</div>
    <div class="divider"></div>
    <ul class="services">
      <p class="services__title">Specialising in</p>
      <li>Risk Insurance</li>
      <li>Debt Management</li>
      <li>Superannuation</li>
      <li>Wealth Creation</li>
      <li>Retirement Planning</li>
    </ul>
    <div class="tag-band">SECURE FUTURE, ENHANCED LIFESTYLE</div>
  </section>

  <section class="card card--back-two">
    <div class="ghost-name" aria-hidden="true">KRWB</div>
    <ul class="services">
      <p class="services__title">Specialising in</p>
      <li>Risk Insurance</li>
      <li>Debt Management</li>
      <li>Superannuation</li>
      <li>Wealth Creation</li>
      <li>Retirement Planning</li>
    </ul>
    <p class="tagline">SECURE FUTURE, ENHANCED LIFESTYLE</p>
  </section>

  <section class="card card--back-three">
    <div class="texture" role="img" aria-label="Dark fine perforated metal texture"></div>
    <div class="brand"><span class="brand__square"></span>KRWB</div>
    <ul class="services">
      <p class="services__title">Specialising in</p>
      <li>Risk Insurance</li>
      <li>Debt Management</li>
      <li>Superannuation</li>
      <li>Wealth Creation</li>
      <li>Retirement Planning</li>
    </ul>
    <p class="tagline">SECURE FUTURE<br>ENHANCED LIFESTYLE</p>
  </section>
</main>
</body>
</html>
```